The quiet harbor with an elephant incorporated in the background

Target Market(s)

Real estate

Industry/Entity Type

Real Estate

Contact Information for Business Card

On back on want my name & number
In front I want the business name, "the quiet harbor", below to say staging & design

Logo Text

The quiet harbor

Font styles to use
Serif

Colors
000000

Requirements
Must have
• I want an elephant behind the writing in gold transperant

```html
<!DOCTYPE html>
<html lang="en">
<head>
<meta charset="utf-8">
<title>The quiet harbor – business card</title>
<link rel="stylesheet" href="https://fonts.googleapis.com/css2?family=Rokkitt:wght@800&family=Josefin+Slab:wght@400&family=Montserrat:wght@500;700&display=swap">
<style>
  :root {
    --ink: #000000;
    --card-black: #060606;
    --paper: #ffffff;
    --gold-light: #f2d36a;
    --gold: #d9ab2c;
    --gold-deep: #b68617;
    --backdrop: #c9c9c9;
  }
  * { margin: 0; padding: 0; box-sizing: border-box; }
  html, body {
    width: 1200px; height: 1200px; overflow: hidden;
    background: var(--backdrop);
  }
  .sheet {
    position: relative; width: 1200px; height: 1200px;
  }
  .card {
    position: absolute; left: 220px; width: 760px; height: 434px;
    overflow: hidden;
    box-shadow: 0 10px 24px rgba(0,0,0,0.18);
  }
  .gold-fill {
    background: linear-gradient(135deg, var(--gold-deep) 0%, var(--gold-light) 30%, var(--gold) 55%, var(--gold-light) 78%, var(--gold-deep) 100%);
  }

  /* Front */
  .card-front { top: 110px; padding: 26px; }
  .card-front .face {
    position: relative; width: 100%; height: 100%;
    background: var(--paper);
  }
  .brand-square {
    position: absolute; left: 236px; top: 42px;
    width: 52px; height: 48px; background: var(--ink);
  }
  .brand-name {
    position: absolute; left: 0; right: 0; top: 176px;
    text-align: center;
    font-family: "Rokkitt", serif; font-weight: 800;
    font-size: 62px; letter-spacing: -1px; line-height: 1;
    color: var(--ink); text-transform: uppercase;
  }
  .brand-tagline {
    position: absolute; left: 0; right: 0; top: 262px;
    text-align: center;
    font-family: "Montserrat", sans-serif; font-weight: 500;
    font-size: 17px; letter-spacing: 22px; padding-left: 22px;
    color: var(--ink); text-transform: uppercase;
  }

  /* Back */
  .card-back { top: 640px; background: var(--card-black); }
  .gold-bar {
    position: absolute; left: 150px; width: 54px;
  }
  .gold-bar.top { top: 0; height: 150px; }
  .gold-bar.bottom { top: 300px; height: 134px; }
  .holder-name {
    position: absolute; left: 316px; top: 62px;
    font-family: "Josefin Slab", serif; font-weight: 400;
    font-size: 48px; letter-spacing: 1px; color: var(--gold);
    text-transform: uppercase;
  }
  .holder-role {
    position: absolute; left: 330px; top: 124px;
    font-family: "Montserrat", sans-serif; font-weight: 700;
    font-size: 15px; color: var(--paper);
  }
  .contact-list {
    position: absolute; left: 420px; top: 204px; list-style: none;
  }
  .contact-list li {
    display: flex; align-items: center; gap: 14px;
    height: 50px;
    font-family: "Josefin Slab", serif; font-size: 24px;
    color: var(--gold);
  }
  .contact-list svg { width: 20px; height: 20px; flex: none; }
</style>
</head>
<body>
<main class="sheet">

  <section class="card card-front gold-fill" aria-label="Card front">
    <div class="face">
      <div class="brand-square"></div>
      <h1 class="brand-name">The quiet harbor</h1>
      <p class="brand-tagline">Staging &amp; design</p>
    </div>
  </section>

  <section class="card card-back" aria-label="Card back">
    <div class="gold-bar top gold-fill"></div>
    <div class="gold-bar bottom gold-fill"></div>

    <h2 class="holder-name">Your name</h2>
    <p class="holder-role">Designation</p>

    <ul class="contact-list">
      <li>
        <svg viewBox="0 0 20 20" aria-hidden="true"><path fill="#fff" d="M5 2l3 4-2 2c1 2 3 4 5 5l2-2 4 3-2 3C9 17 3 11 2 5z"/></svg>
        1234-5678-9101
      </li>
      <li>
        <svg viewBox="0 0 20 20" aria-hidden="true"><rect x="2" y="5" width="16" height="11" fill="#fff"/><path d="M2 5l8 6 8-6" fill="none" stroke="#060606" stroke-width="1.5"/></svg>
        info@thequietharbor.com
      </li>
      <li>
        <svg viewBox="0 0 20 20" aria-hidden="true"><circle cx="10" cy="10" r="8" fill="#fff"/><path d="M2 10h16M10 2v16M4 6h12M4 14h12M10 2c-4 4-4 12 0 16M10 2c4 4 4 12 0 16" fill="none" stroke="#060606" stroke-width="1"/></svg>
        www.thequietharbor.com
      </li>
    </ul>
  </section>

</main>
</body>
</html>
```